Health Care Company with Logo Needs Business Cards designed

We are a luxury behavioral health company looking for business cards design we already have a logo and are looking for someone to design a sophisticated luxurious looking business card. Please note that Card design should be captivating just like the logo and also encompass the logo color

Industry/Entity Type

Healthcare

Contact Information for Business Card

Logo,company name, tagline, my name and title, contact details, and physical address

```html
<!DOCTYPE html>
<html lang="en">
<head>
<meta charset="utf-8">
<title>Marlow Wellness Group – Business Card</title>
<link rel="stylesheet" href="https://fonts.googleapis.com/css2?family=Roboto:wght@400;700&family=Roboto+Condensed:wght@700&display=swap">
<style>
  :root {
    --backdrop: #3c3c3c;
    --card: #161616;
    --card-pattern: #1f1f1f;
    --edge-blue: #12a7ea;
    --brand-purple: #8a3fb5;
    --tagline-blue: #1c9ad6;
    --ink-light: #e6e6e6;
    --icon-orange: #f39a1e;
    --icon-green: #7cc242;
  }
  * { box-sizing: border-box; margin: 0; padding: 0; }
  html, body {
    width: 1200px; height: 801px; overflow: hidden;
    background: var(--backdrop);
    font-family: "Roboto", Arial, sans-serif;
  }
  .stage {
    width: 1200px; height: 801px;
    display: flex; align-items: center; justify-content: center; gap: 40px;
  }
  .card {
    position: relative;
    width: 540px; height: 309px;
    background: var(--card);
    border-left: 3px solid var(--edge-blue);
    border-bottom: 3px solid var(--edge-blue);
    box-shadow: 0 14px 30px rgba(0,0,0,.45);
    overflow: hidden;
  }
  .brand {
    position: absolute; top: 52px; right: 70px; text-align: left;
  }
  .brand-name {
    display: flex; align-items: center; gap: 10px;
    font-family: "Roboto Condensed", Arial, sans-serif;
    font-weight: 700; font-size: 28px; color: var(--brand-purple);
    white-space: nowrap;
  }
  .brand-mark {
    width: 14px; height: 14px; background: var(--brand-purple);
  }
  .brand-tagline {
    margin-top: 4px; margin-left: 24px;
    font-size: 8px; letter-spacing: 2px; text-transform: uppercase;
    font-weight: 700; color: var(--tagline-blue);
    white-space: nowrap;
  }
  .person { position: absolute; left: 40px; top: 168px; }
  .person-name {
    font-family: "Roboto Condensed", Arial, sans-serif;
    font-weight: 700; font-size: 19px; text-transform: uppercase;
    color: var(--edge-blue); letter-spacing: .5px;
  }
  .person-title { font-size: 14px; color: var(--ink-light); margin-top: 2px; }
  .divider {
    position: absolute; left: 40px; right: 30px; top: 222px;
    height: 1px; background: var(--edge-blue);
  }
  .contacts {
    position: absolute; left: 40px; top: 234px;
    list-style: none; font-size: 13px; color: var(--ink-light); line-height: 20px;
  }
  .contacts li { display: flex; align-items: center; gap: 8px; }
  .contacts svg { width: 11px; height: 11px; flex: none; }
  .address {
    position: absolute; right: 30px; top: 236px;
    text-align: right; font-size: 13px; color: var(--ink-light); line-height: 18px;
    font-style: normal;
  }
  .card-back .pattern {
    position: absolute; inset: 0;
    background: linear-gradient(135deg, #0f0f0f 0%, var(--card-pattern) 55%, #262626 100%);
  }
  .card-back .brand-name {
    position: absolute; right: 40px; top: 136px; font-size: 24px;
  }
</style>
</head>
<body>
<main class="stage">
  <section class="card card-front" aria-label="Card front">
    <div class="brand">
      <div class="brand-name"><span class="brand-mark"></span>Marlow Wellness Group</div>
      <div class="brand-tagline">Committed to calm, care and renewal</div>
    </div>
    <div class="person">
      <div class="person-name">Daniel Reyes</div>
      <div class="person-title">President</div>
    </div>
    <div class="divider"></div>
    <ul class="contacts">
      <li>
        <svg viewBox="0 0 12 12"><path d="M2.5 1 L4.5 1 L5.2 3.6 L4 4.6 Q5 7 7.4 8 L8.4 6.8 L11 7.5 L11 9.5 Q10.5 11 9 11 Q1 10 1 3 Q1 1.5 2.5 1Z" fill="var(--icon-orange)"/></svg>
        555-013-0188
      </li>
      <li>
        <svg viewBox="0 0 12 12"><rect x="0.5" y="2" width="11" height="8" fill="var(--icon-green)"/><path d="M0.5 2 L6 6.5 L11.5 2" fill="none" stroke="var(--card)" stroke-width="1"/></svg>
        hello@marlowwellness.com
      </li>
      <li>
        <svg viewBox="0 0 12 12"><circle cx="6" cy="6" r="5.2" fill="none" stroke="var(--brand-purple)" stroke-width="1.4"/><path d="M1 6 H11 M6 1 Q3 6 6 11 Q9 6 6 1" fill="none" stroke="var(--brand-purple)" stroke-width="1"/></svg>
        www.marlowwellness.com
      </li>
    </ul>
    <address class="address">
      1820 Harbor View Lane<br>Lakeside CA 90000
    </address>
  </section>

  <section class="card card-back" aria-label="Card back">
    <div class="pattern" role="img" aria-label="Tonal repeating brand-mark pattern in dark greys"></div>
    <div class="brand-name">Marlow Wellness Group</div>
  </section>
</main>
</body>
</html>
```